TA BRAMLEY BUSINESS CARD DESIGN PROJECT

We need to utilize our logo that was expertly created on PixelHarbor and now need to match this with a business card design.

```html
<!DOCTYPE html>
<html lang="en">
<head>
<meta charset="utf-8">
<title>TA BRAMLEY Business Card</title>
<link href="https://fonts.googleapis.com/css2?family=Open+Sans:wght@400;700&display=swap" rel="stylesheet">
<style>
  :root {
    --brand-blue: #1a58b3;
    --ink: #1b1b1b;
    --paper: #ffffff;
    --backdrop: #232323;
    --rule: #2a2a2a;
  }
  * { box-sizing: border-box; margin: 0; padding: 0; }
  html, body {
    width: 1200px; height: 780px; overflow: hidden;
    background: var(--backdrop);
    font-family: "Open Sans", Arial, sans-serif;
  }
  .canvas {
    width: 1200px; height: 780px;
    display: flex; align-items: center; justify-content: center; gap: 60px;
  }
  .card {
    width: 520px; height: 300px; position: relative; overflow: hidden;
  }
  /* Front */
  .card-front { background: var(--paper); }
  .brand-block {
    position: absolute; left: 0; top: 70px; width: 250px;
    text-align: center;
  }
  .brand-name {
    color: var(--brand-blue); font-weight: 700; font-size: 32px;
    letter-spacing: 2px; line-height: 1;
  }
  .divider {
    position: absolute; left: 262px; top: 44px; width: 1px; height: 170px;
    background: var(--rule);
  }
  .contact-block { position: absolute; left: 290px; top: 58px; }
  .person-name {
    color: var(--brand-blue); font-weight: 700; font-size: 25px; line-height: 1.1;
  }
  .person-title { color: var(--ink); font-size: 14px; margin-top: 2px; }
  .contact-list { list-style: none; margin-top: 16px; }
  .contact-list li {
    display: flex; align-items: center; gap: 7px;
    color: var(--ink); font-size: 14px; line-height: 1.6;
  }
  .contact-list svg { width: 12px; height: 12px; fill: var(--brand-blue); flex: none; }
  .address-band {
    position: absolute; left: 0; bottom: 18px; width: 400px; height: 28px;
    background: var(--brand-blue); color: var(--paper);
    font-size: 13px; line-height: 28px; padding-left: 22px;
  }
  .band-brand {
    position: absolute; left: 410px; bottom: 22px;
    color: var(--brand-blue); font-weight: 700; font-size: 15px; letter-spacing: 1px;
  }
  /* Back */
  .card-back { background: var(--brand-blue); }
  .back-pattern {
    position: absolute; inset: 0;
    background: linear-gradient(135deg, #2463c0 0%, #1a58b3 50%, #144a9c 100%);
  }
  .back-brand {
    position: absolute; right: 40px; bottom: 40px;
    color: var(--paper); font-weight: 700; font-size: 18px; letter-spacing: 2px;
  }
</style>
</head>
<body>
<main class="canvas">
  <section class="card card-front" aria-label="Business card front">
    <div class="brand-block"><div class="brand-name">TA BRAMLEY</div></div>
    <div class="divider"></div>
    <div class="contact-block">
      <h1 class="person-name">Marta Kovalenko</h1>
      <p class="person-title">Managing Director</p>
      <ul class="contact-list">
        <li>
          <svg viewBox="0 0 24 24" aria-hidden="true"><path d="M6.6 10.8a15.1 15.1 0 0 0 6.6 6.6l2.2-2.2a1 1 0 0 1 1-.25 11.4 11.4 0 0 0 3.6.57 1 1 0 0 1 1 1V20a1 1 0 0 1-1 1A17 17 0 0 1 3 4a1 1 0 0 1 1-1h3.5a1 1 0 0 1 1 1c0 1.25.2 2.45.57 3.57a1 1 0 0 1-.25 1z"/></svg>
          (555) 214-0736
        </li>
        <li>
          <svg viewBox="0 0 24 24" aria-hidden="true"><path d="M2 5h20v14H2zm2 2v.5l8 5 8-5V7l-8 5z"/></svg>
          hello@tabramley.com
        </li>
        <li>
          <svg viewBox="0 0 24 24" aria-hidden="true"><circle cx="12" cy="12" r="10"/></svg>
          www.tabramley.com
        </li>
      </ul>
    </div>
    <div class="address-band">418 Linden Ave. Suite 300 Fort Worth, TX 76104</div>
    <div class="band-brand">TA BRAMLEY</div>
  </section>

  <section class="card card-back" aria-label="Business card back">
    <div class="back-pattern" role="img" aria-label="Repeating pattern of the brand mark in lighter and darker blues"></div>
    <div class="back-brand">TA BRAMLEY</div>
  </section>
</main>
</body>
</html>
```